Business Card Design needed for start up company Halvora

In need of a new business card designed for a start up company based in Sydney, Halvora is a new start up innovative Company, our mission it to make property accessible for everyday Australian and to become the leading Real Estate platform in Australia. We want it to be fresh and clean.

Industry/Entity Type

Financial

Contact Information for Business Card

Section for Name
Section for Title

HALVORA - The Strength of Pooling
Mobile:
Direct:

Font styles to use
Sans Serif

Colors
33a6d7
0692cd
0255a3
ffffff

Requirements
Must have
• Logo, all business card details

```html
<!DOCTYPE html>
<html lang="en">
<head>
<meta charset="utf-8">
<title>Halvora Business Card</title>
<link href="https://fonts.googleapis.com/css2?family=Roboto:wght@400;500;700&display=swap" rel="stylesheet">
<style>
  :root {
    --sky: #33a6d7;
    --azure: #0692cd;
    --navy: #0255a3;
    --deep-navy: #1f3f78;
    --white: #ffffff;
    --paper: #f4f4f4;
    --ink: #4a4a4a;
    --rule: #777777;
    --backdrop: #2b2b2b;
  }
  * { margin: 0; padding: 0; box-sizing: border-box; }
  html, body {
    width: 1200px; height: 886px; overflow: hidden;
    background: var(--backdrop);
    font-family: 'Roboto', sans-serif;
  }
  .stage { position: relative; width: 1200px; height: 886px; }

  .card {
    position: absolute;
    width: 560px; height: 320px;
    border-radius: 22px;
    box-shadow: 0 14px 30px rgba(0,0,0,0.45);
  }

  .brand-name {
    font-weight: 700; line-height: 1; letter-spacing: 2px;
  }

  /* Back side */
  .card-back {
    left: 90px; top: 110px;
    background: var(--deep-navy);
    color: var(--white);
  }
  .card-back .brand-name {
    position: absolute; left: 0; right: 0; top: 118px;
    text-align: center; font-size: 50px; color: var(--white);
  }
  .tagline {
    position: absolute; left: 0; right: 0; top: 218px;
    text-align: center; font-size: 17px; letter-spacing: 0.5px;
  }

  /* Front side */
  .card-front {
    left: 550px; top: 450px;
    background: var(--paper);
    color: var(--ink);
  }
  .card-front .brand-name {
    position: absolute; right: 40px; top: 58px;
    font-size: 42px; color: var(--deep-navy);
  }

  .person { position: absolute; left: 40px; top: 128px; }
  .person-name {
    font-weight: 700; font-size: 21px; color: var(--deep-navy); letter-spacing: 0.3px;
  }
  .person-title {
    font-size: 15px; color: var(--azure); letter-spacing: 0.6px; margin-top: 2px;
  }

  .contacts { position: absolute; left: 40px; top: 192px; list-style: none; }
  .contacts li {
    display: flex; align-items: center; gap: 9px;
    font-size: 15px; line-height: 21px; color: var(--ink);
  }
  .contacts svg { width: 13px; height: 13px; fill: var(--deep-navy); flex: none; }

  .divider {
    position: absolute; left: 250px; top: 226px;
    width: 1px; height: 44px; background: var(--rule);
  }
  .address {
    position: absolute; left: 268px; top: 226px;
    font-size: 16px; line-height: 22px; color: var(--ink); font-style: normal;
  }
</style>
</head>
<body>
<main class="stage">

  <section class="card card-back" aria-label="Card back">
    <p class="brand-name">HALVORA</p>
    <p class="tagline">The Strength of Pooling</p>
  </section>

  <section class="card card-front" aria-label="Card front">
    <p class="brand-name">HALVORA</p>

    <div class="person">
      <p class="person-name">LIAM CARVER</p>
      <p class="person-title">CEO/FOUNDER</p>
    </div>

    <ul class="contacts">
      <li>
        <svg viewBox="0 0 24 24" aria-hidden="true"><path d="M6.6 10.8c1.4 2.8 3.8 5.1 6.6 6.6l2.2-2.2c.3-.3.7-.4 1-.2 1.1.4 2.3.6 3.6.6.6 0 1 .4 1 1V20c0 .6-.4 1-1 1C10.6 21 3 13.4 3 4c0-.6.4-1 1-1h3.5c.6 0 1 .4 1 1 0 1.3.2 2.5.6 3.6.1.3 0 .7-.2 1l-2.3 2.2z"/></svg>
        0412 508 317
      </li>
      <li>
        <svg viewBox="0 0 24 24" aria-hidden="true"><path d="M7 1h10a2 2 0 0 1 2 2v18a2 2 0 0 1-2 2H7a2 2 0 0 1-2-2V3a2 2 0 0 1 2-2zm0 3v14h10V4H7zm5 15.5a1 1 0 1 0 0 2 1 1 0 0 0 0-2z"/></svg>
        02 8 615 4470
      </li>
      <li>
        <svg viewBox="0 0 24 24" aria-hidden="true"><path d="M2 5h20v14H2V5zm2 2v.5l8 5 8-5V7H4z"/></svg>
        liam@halvora.com
      </li>
      <li>
        <svg viewBox="0 0 24 24" aria-hidden="true"><path d="M12 2a10 10 0 1 0 0 20 10 10 0 0 0 0-20zm0 2c1 0 2.3 2 2.8 5H9.2C9.7 6 11 4 12 4zm-7.7 7h3c0 1 .1 1.5.2 2h-3a8 8 0 0 1-.2-2zm3.4 4c.4 2 1 3.3 1.6 4.3A8 8 0 0 1 5 15h2.7zM12 20c-1 0-2.3-2-2.8-5h5.6C14.3 18 13 20 12 20zm3-4.7c.6-1 1.2-2.3 1.6-4.3H19a8 8 0 0 1-4 4.3zM16.7 13c.1-.5.2-1 .2-2h3a8 8 0 0 1-.2 2h-3z"/></svg>
        www.halvora.com
      </li>
    </ul>

    <span class="divider"></span>
    <address class="address">
      18 Wattle Street<br>
      Sydney, NSW 2000
    </address>
  </section>

</main>
</body>
</html>
```